Veterinary Pylon

My veterinary clinic is not clearly visible from the street and I want to place a Pylon next to my driveway. I want a modern, elegant straight Design, the Photo shows the sheduled place. One can see the clinic on our Homepage: www.tailbright-vethaus.at
The last pictures are examples for pylones I like

Target Market(s)

the passing cars often miss my entry...I want to show where to turn left

Colors
3276b5
33a6d7
00a990

Requirements
Must have
• High value, simple elegance, size: 250cm (high) x 100cm (width)
Nice to have
• Our Logo, arrow(?)

A special Text is not necessary but this will be an option:

Biegen sie hier ab und wir biegen es wieder hin!
Should not have
• Too much Color, the colors I have chosen are the possible colors but it‘s not necessary to use them.

```html
<!DOCTYPE html>
<html lang="de">
<head>
<meta charset="utf-8">
<title>Tailbright Vethaus – Pylon</title>
<link href="https://fonts.googleapis.com/css2?family=Krona+One&display=swap" rel="stylesheet">
<style>
  :root {
    --brand-navy: #124a93;
    --brand-cyan: #2dbde0;
    --panel-white: #ffffff;
    --ground-tint: #f2f6fb;
  }
  html, body {
    margin: 0;
    padding: 0;
    width: 1200px;
    height: 3000px;
    overflow: hidden;
    background: var(--panel-white);
  }
  .pylon {
    position: relative;
    width: 1200px;
    height: 3000px;
    box-sizing: border-box;
    padding: 26px;
    background: linear-gradient(180deg, var(--brand-cyan) 0%, #259fcf 38%, #1a6fb0 62%, var(--brand-navy) 85%);
  }
  .pylon__face {
    position: relative;
    width: 100%;
    height: 100%;
    background: var(--panel-white);
    overflow: hidden;
  }
  .brand-mark {
    position: absolute;
    left: 384px;
    top: 150px;
    width: 380px;
    height: 380px;
    border-radius: 50%;
    background: var(--brand-cyan);
  }
  .brand-name {
    position: absolute;
    top: 660px;
    left: 0;
    width: 100%;
    margin: 0;
    text-align: center;
    font-family: "Krona One", sans-serif;
    font-weight: 400;
    color: var(--brand-navy);
    font-size: 80px;
    line-height: 1.45;
    letter-spacing: 0;
  }
  .ground-arc {
    position: absolute;
    left: 0;
    top: 1480px;
    width: 1148px;
    height: 1468px;
  }
  .turn-arrow {
    position: absolute;
    left: 436px;
    top: 1579px;
    width: 280px;
    height: 218px;
  }
</style>
</head>
<body>
  <main class="pylon">
    <div class="pylon__face">
      <div class="brand-mark" aria-hidden="true"></div>
      <h1 class="brand-name">TAILBRIGHT<br>VETHAUS</h1>

      <svg class="ground-arc" viewBox="0 0 1148 1468" aria-hidden="true">
        <path d="M0 236 Q574 -130 1148 236 L1148 1468 L0 1468 Z" fill="var(--ground-tint)"/>
        <path d="M0 228 Q574 -150 1148 228" fill="none" stroke="var(--brand-cyan)" stroke-width="12"/>
      </svg>

      <svg class="turn-arrow" viewBox="0 0 280 218" role="img" aria-label="Pfeil nach links – hier abbiegen">
        <defs>
          <linearGradient id="arrowFade" x1="0" y1="0" x2="1" y2="0">
            <stop offset="0" stop-color="#1a6fb0"/>
            <stop offset="1" stop-color="#2dbde0"/>
          </linearGradient>
        </defs>
        <path d="M110 0 L110 33 L44 98 L280 98 L280 120 L44 120 L110 185 L110 218 L0 109 Z" fill="url(#arrowFade)"/>
      </svg>
    </div>
  </main>
</body>
</html>
```